Quill Physical Therapy Website

I would need a clean modern website built to showcase my Physical therapy brand and services. I would need a simple but descriptive website that can ultimately connect my patients to my electronic medical portal so they may book an appointment..

```html
<!DOCTYPE html>
<html lang="en">
<head>
<meta charset="utf-8">
<title>Quill Physical Therapy</title>
<link href="https://fonts.googleapis.com/css2?family=League+Spartan:wght@400;500;600;700&family=Open+Sans:wght@400;600&display=swap" rel="stylesheet">
<style>
:root{
  --teal:#137470;
  --green:#77c043;
  --green-soft:#c5e3ad;
  --black:#000;
  --ink:#333;
  --white:#fff;
  --head:'League Spartan',sans-serif;
  --body:'Open Sans',sans-serif;
}
*{margin:0;padding:0;box-sizing:border-box}
html,body{width:1200px;height:2448px;overflow:hidden;background:var(--white)}
body{position:relative;font-family:var(--body);color:var(--ink)}
.abs{position:absolute}
.btn{position:absolute;background:var(--green);color:var(--white);font-family:var(--head);font-weight:600;border-radius:24px;display:flex;align-items:center;justify-content:center;font-size:16px}

/* hero */
.hero{left:0;top:0;width:1200px;height:596px;background:var(--black);overflow:hidden}
.hero-photo{left:470px;top:0;width:730px;height:596px;background:radial-gradient(ellipse at 70% 35%,#8a8a8a 0%,#4a4a4a 35%,#1a1a1a 65%,#000 85%)}
.nav a{position:absolute;top:50px;color:var(--white);font-family:var(--head);font-weight:600;font-size:16px;text-decoration:none}
.nav a.active{color:var(--green);border-bottom:2px solid var(--green);padding-bottom:6px}
.logo-tab{left:512px;top:0;width:175px;height:184px;background:var(--white);border-radius:0 0 70px 70px;display:flex;flex-direction:column;align-items:center;justify-content:center;gap:10px}
.logo-tab .mark{width:44px;height:44px;border-radius:50%;background:var(--teal)}
.logo-tab .name{font-family:var(--head);font-weight:700;font-size:30px;color:var(--teal)}
.social-top{top:53px;width:16px;height:16px;border-radius:50%;border:2px solid var(--green)}
.welcome{left:116px;top:206px;color:var(--white);font-family:var(--head);font-weight:600;font-size:36px}
.brand-big{left:110px;top:246px;color:var(--teal);font-family:var(--head);font-weight:700;font-size:150px;line-height:1;letter-spacing:2px}
.subtitle{left:113px;top:380px;color:var(--white);font-family:var(--head);font-weight:600;font-size:37px}

/* what we do */
.side-band{left:0;top:596px;width:112px;height:464px;background:var(--green)}
.side-band span{position:absolute;left:56px;top:232px;transform:translate(-50%,-50%) rotate(-90deg);white-space:nowrap;color:var(--white);font-family:var(--head);font-weight:700;font-size:58px}
.about-photo{left:112px;top:596px;width:976px;height:464px;background:linear-gradient(120deg,#fbf7f3 0%,#f3e9e2 40%,#e7eef6 60%,#f7f2ee 100%)}
.right-shape{left:1088px;top:596px;width:112px;height:464px}
.about-text{left:157px;top:672px;width:730px;font-size:14.4px;line-height:24px;color:#444}
.about-text p{margin-bottom:24px}

/* services */
.section-title{left:0;top:1138px;width:1200px;text-align:center;font-family:var(--head);font-weight:700;font-size:60px;color:var(--teal)}
.section-lead{left:200px;top:1208px;width:800px;text-align:center;font-size:14.4px;line-height:24px;color:#444}
.service{top:1300px;width:290px;text-align:center}
.service .ring{width:128px;height:128px;margin:0 auto;border-radius:50%;border:2px solid var(--green);padding:4px}
.service .ring div{width:100%;height:100%;border-radius:50%;background:var(--green);display:flex;align-items:center;justify-content:center}
.service h3{margin-top:22px;font-family:var(--head);font-weight:600;font-size:19px;color:var(--teal)}
.service p{margin-top:10px;font-size:13.5px;line-height:18px;color:#444}

/* contact */
.teal-right{left:1088px;top:1649px;width:112px;height:470px;background:var(--teal)}
.teal-bottom{left:0;top:2112px;width:1200px;height:336px;background:var(--teal)}
.contact-photo{left:110px;top:1649px;width:978px;height:567px;background:linear-gradient(135deg,#f6f3f0 0%,#efe6de 45%,#f4efea 70%,#fbfaf8 100%)}
.eyebrow{left:145px;top:1714px;font-family:var(--head);font-weight:600;font-size:17px;color:var(--teal)}
.contact-title{left:145px;top:1744px;font-family:var(--head);font-size:37px;color:var(--teal)}
.contact-title b{font-weight:700}
.contact-lead{left:146px;top:1788px;width:500px;font-size:14.4px;line-height:24px;color:#444}
.info{left:145px;display:flex;align-items:center;gap:18px;font-size:17px;color:#222;line-height:28px}
.info .ico{width:40px;height:40px;border-radius:50%;background:var(--teal);display:flex;align-items:center;justify-content:center;flex:none}
.social{top:2089px;width:32px;height:32px;border-radius:50%}
.form{left:650px;top:1725px;width:376px;height:388px;background:var(--white);box-shadow:0 2px 10px rgba(0,0,0,.12)}
.field{position:absolute;left:29px;width:316px;height:38px;border:1px solid #ccc;font-size:12px;color:#444;padding:11px 8px}
.submit{position:absolute;left:118px;top:315px;width:236px;height:44px;background:var(--teal);color:var(--white);border-radius:24px;font-family:var(--head);font-weight:500;font-size:15px;letter-spacing:3px;display:flex;align-items:center;justify-content:center;gap:12px}

/* footer */
.foot-logo{left:112px;top:2262px;width:130px;display:flex;flex-direction:column;align-items:center;gap:14px}
.foot-logo .mark{width:60px;height:60px;border-radius:50%;background:var(--white)}
.foot-logo .name{font-family:var(--head);font-weight:700;font-size:38px;color:var(--white)}
.foot-nav a{position:absolute;top:2293px;color:var(--white);font-size:16px;text-decoration:none}
.copyright{left:700px;top:2333px;width:390px;text-align:right;color:var(--white);font-size:14px}
</style>
</head>
<body>

<header class="abs hero">
  <div class="abs hero-photo" role="img" aria-label="Black and white photo of a therapist's hand on an athlete's shoulder"></div>
  <nav class="nav">
    <a class="active" style="left:110px">Home</a>
    <a style="left:190px">What We Do</a>
    <a style="left:315px">Blog</a>
    <a style="left:382px">Contact Us</a>
  </nav>
  <div class="abs logo-tab"><div class="mark"></div><div class="name">QUILL</div></div>
  <div class="btn" style="left:776px;top:40px;width:212px;height:43px">Book an Appointment</div>
  <div class="abs social-top" style="left:1013px"></div>
  <div class="abs social-top" style="left:1042px"></div>
  <div class="abs social-top" style="left:1070px"></div>
  <div class="abs welcome">WELCOME TO</div>
  <div class="abs brand-big">QUILL</div>
  <div class="abs subtitle">PHYSICAL THERAPY</div>
  <div class="btn" style="left:115px;top:437px;width:213px;height:44px">Book an Appointment</div>
</header>

<section>
  <div class="abs side-band"><span>WHAT WE DO</span></div>
  <div class="abs about-photo" role="img" aria-label="Faded photo of a therapist massaging a patient's back"></div>
  <svg class="abs right-shape" viewBox="0 0 112 464" aria-hidden="true">
    <polygon points="0,114 112,100 112,464 0,464" fill="var(--green-soft)"/>
    <polygon points="0,0 112,0 112,60 90,64 0,104" fill="var(--white)"/>
    <path d="M52 34v26M44 52l8 10 8-10" stroke="var(--green)" stroke-width="4" fill="none"/>
  </svg>
  <div class="abs about-text">
    <p>Sed ut perspiciatis unde omnis iste natus error sit voluptatem accusantium doloremque laudantium, totam rem aperiam, eaque ipsa quae ab illo inventore veritatis et quasi architecto beatae vitae dicta sunt explicabo. Nemo enim ipsam voluptatem quia voluptas sit aspernatur aut odit aut fugit, sed quia consequuntur magni dolores eos qui ratione voluptatem sequi nesciunt.</p>
    <p>Neque porro quisquam est, qui dolorem ipsum quia dolor sit amet, consectetur, adipisci velit, sed quia non numquam eius modi tempora incidunt ut labore et dolore magnam aliquam quaerat voluptatem. Ut enim ad minima veniam, quis nostrum exercitationem ullam corporis suscipit laboriosam, nisi ut aliquid ex ea commodi consequatur? Quis autem vel eum iure reprehenderit qui in ea voluptate velit esse quam nihil molestiae consequatur, vel illum qui dolorem eum fugiat quo voluptas nulla pariatur</p>
  </div>
  <div class="btn" style="left:158px;top:935px;width:178px;height:44px">How It's Work?</div>
</section>

<section>
  <h2 class="abs section-title">FINIBUS BONORUM ET</h2>
  <p class="abs section-lead">Sed ut perspiciatis unde omnis iste natus error sit voluptatem accusantium doloremque laudantium, totam rem aperiam, eaque ipsa quae ab illo inventore veritatis et quasi architecto beatae vitae dicta sunt explicabo. Nemo enim ipsam voluptatem quia voluptas sit aspernatur aut odit aut fugit.</p>

  <div class="abs service" style="left:104px">
    <div class="ring"><div>
      <svg width="60" height="56" viewBox="0 0 60 56" fill="none" stroke="#1d4a3a" stroke-width="3"><rect x="3" y="8" width="54" height="45" rx="3"/><path d="M3 20h54M15 3v10M45 3v10"/><circle cx="30" cy="37" r="11"/><path d="M24 37l4 4 8-8"/></svg>
    </div></div>
    <h3>Make An Appointment</h3>
    <p>Lorem ipsum dolor sit amet, consectetur adipiscing elit, sed do eiusmod tempor incididunt ut labore et dolore magna aliqua. Ut enim ad minim veniam</p>
  </div>
  <div class="abs service" style="left:454px">
    <div class="ring"><div><div style="width:46px;height:46px;border-radius:50%;background:#1d4a3a"></div></div></div>
    <h3>Quill Physical</h3>
    <p>Lorem ipsum dolor sit amet, consectetur adipiscing elit, sed do eiusmod tempor incididunt ut labore et dolore magna aliqua. Ut enim ad minim veniam</p>
  </div>
  <div class="abs service" style="left:804px">
    <div class="ring"><div role="img" aria-label="Icon of a therapist treating a patient on a table">
      <svg width="70" height="60" viewBox="0 0 70 60" fill="#1d4a3a"><circle cx="24" cy="10" r="7"/><circle cx="56" cy="34" r="6"/><rect x="4" y="40" width="62" height="8" rx="2"/><rect x="8" y="48" width="5" height="10"/><rect x="57" y="48" width="5" height="10"/><rect x="14" y="20" width="18" height="18" rx="3"/></svg>
    </div></div>
    <h3>Deep Therapy</h3>
    <p>Lorem ipsum dolor sit amet, consectetur adipiscing elit, sed do eiusmod tempor incididunt ut labore et dolore magna aliqua. Ut enim ad minim veniam</p>
  </div>
</section>

<section>
  <div class="abs teal-right"></div>
  <div class="abs teal-bottom"></div>
  <div class="abs contact-photo" role="img" aria-label="Faded photo of a therapist treating a patient's shoulder"></div>
  <div class="abs eyebrow">GET IN TOUCH WITH US!</div>
  <h2 class="abs contact-title" style="font-weight:400">GET YOUR <b>LIFESTYLE BACK!</b></h2>
  <p class="abs contact-lead">Sed ut perspiciatis unde omnis iste natus error sit voluptatem accusantium doloremque laudantium, totam rem aperiam,</p>

  <div class="abs info" style="top:1860px">
    <span class="ico"><svg width="16" height="20" viewBox="0 0 16 20"><path d="M8 0a8 8 0 0 0-8 8c0 6 8 12 8 12s8-6 8-12a8 8 0 0 0-8-8z" fill="#fff"/><circle cx="8" cy="8" r="3" fill="var(--teal)"/></svg></span>
    <span>418 Birchwood Lane, Fairhaven,<br>NC, North Carolina, 28590.</span>
  </div>
  <div class="abs info" style="top:1937px">
    <span class="ico"><svg width="18" height="18" viewBox="0 0 24 24"><path d="M6.6 10.8a15 15 0 0 0 6.6 6.6l2.2-2.2c.3-.3.7-.4 1-.2 1.1.4 2.3.6 3.6.6.6 0 1 .4 1 1V20c0 .6-.4 1-1 1A17 17 0 0 1 3 4c0-.6.4-1 1-1h3.5c.6 0 1 .4 1 1 0 1.3.2 2.5.6 3.6.1.3 0 .7-.2 1z" fill="#fff"/></svg></span>
    <span>910-555-0143</span>
  </div>
  <div class="abs info" style="top:2004px">
    <span class="ico"><svg width="18" height="14" viewBox="0 0 18 14"><rect width="18" height="14" rx="2" fill="#fff"/><path d="M1 2l8 6 8-6" stroke="var(--teal)" stroke-width="2" fill="none"/></svg></span>
    <span>hello@quillpt.example</span>
  </div>
  <div class="abs social" style="left:147px;background:#0e66a8"></div>
  <div class="abs social" style="left:190px;background:#c4161c"></div>
  <div class="abs social" style="left:234px;background:#2b4c8c"></div>
  <div class="abs social" style="left:278px;background:#3ca0e0"></div>

  <form class="abs form">
    <div class="field" style="top:32px">First Name</div>
    <div class="field" style="top:76px">Laste Name</div>
    <div class="field" style="top:121px">Phone</div>
    <div class="field" style="top:165px">Email</div>
    <div class="field" style="top:210px;height:97px;padding:12px 14px">Message Here...</div>
    <div class="submit">SUBMIT NOW <svg width="14" height="10" viewBox="0 0 14 10"><path d="M0 5h11M8 1l4 4-4 4" stroke="#fff" stroke-width="2" fill="none"/></svg></div>
  </form>
</section>

<footer>
  <div class="abs foot-logo"><div class="mark"></div><div class="name">QUILL</div></div>
  <nav class="foot-nav">
    <a style="left:751px">Home</a>
    <a style="left:827px">What We Do</a>
    <a style="left:948px">Blog</a>
    <a style="left:1012px">Contact Us</a>
  </nav>
  <div class="abs copyright">Quill Physical Therapy © 2021 All Rights Reserved.</div>
</footer>

</body>
</html>
```